Los Angeles based Demolition, Grading, and Structural concrete Contractor in need of a Sale brochure

We are a Los Angeles-based demolition, grading, and structural concrete contractor looking for a professionally designed sales brochure that represents our company and services. The brochure should be visually appealing, easy to read, and include the following:

-Company Logo: Prominently displayed to enhance brand identity.

-Services We Offer: A clear breakdown of our key services, including demolition, grading, and structural concrete work.

-Project Scope & Capabilities: A brief explanation of the type of projects we handle (residential, commercial, industrial).

-Pricing Information: Mention that demolition services start at $20,000. This price includes complete demolition of structure, safe debris removal and hauling, site preparation for new construction.

-Contact Information: Our phone number(818.502.6617), email(contact@brovanbuildersinc.example) , and website for potential clients to reach out.

The design should reflect the professionalism and strength of our industry, using a modern, clean layout with bold colors that align with construction and demolition themes. Images of past work or stock photos representing our services are encouraged.

Final deliverables should be print-ready (PDF) and digital-friendly formats. Looking forward to creative and impactful designs!

```html
<!DOCTYPE html>
<html lang="en">
<head>
<meta charset="utf-8">
<title>Brovan Builders – Brochure Spread</title>
<link href="https://fonts.googleapis.com/css2?family=Arimo:wght@400;700&display=swap" rel="stylesheet">
<style>
  :root {
    --bg: #8a8a8a;
    --brand-blue: #1363b4;
    --brand-blue-light: #3f8fd6;
    --line-blue: #2f86d8;
    --panel: #e9e9ea;
    --paper: #f3f3f3;
    --bar-grey: #8f8f92;
    --text-grey: #7d7d80;
    --white: #ffffff;
  }
  * { box-sizing: border-box; margin: 0; padding: 0; }
  html, body { width: 1200px; height: 1200px; overflow: hidden; }
  body { background: var(--bg); font-family: "Arimo", Arial, sans-serif; position: relative; }

  .spread { position: absolute; left: 100px; top: 250px; width: 1000px; height: 700px; display: flex; box-shadow: 0 18px 40px rgba(0,0,0,.25); }
  .page { position: relative; width: 500px; height: 700px; overflow: hidden; }

  /* Cover (left) */
  .cover { background: var(--brand-blue); }
  .cover__panel { position: absolute; left: 125px; top: 0; width: 190px; height: 300px; background: var(--panel); display: flex; align-items: flex-end; justify-content: center; padding-bottom: 36px; }
  .wordmark { font-weight: 700; font-size: 22px; letter-spacing: .5px; display: flex; align-items: center; gap: 6px; }
  .wordmark__square { width: 12px; height: 12px; }
  .cover .wordmark { color: var(--brand-blue); }
  .cover .wordmark__square { background: var(--brand-blue); }
  .cover__contact { position: absolute; left: 0; right: 0; top: 325px; color: var(--white); font-weight: 700; display: flex; flex-direction: column; align-items: center; gap: 14px; }
  .contact-line { display: flex; align-items: center; gap: 10px; }
  .contact-line--phone { font-size: 34px; letter-spacing: 1px; }
  .contact-line--email { font-size: 17px; }
  .icon-phone { width: 30px; height: 30px; }
  .icon-globe { width: 16px; height: 16px; }

  /* Inside (right) */
  .inside { background: var(--paper); }
  .rule { position: absolute; background: var(--line-blue); }
  .rule--vertical { left: 30px; top: 20px; width: 1.5px; height: 310px; }
  .rule--dot { left: 27px; top: 328px; width: 7px; height: 7px; border-radius: 50%; }
  .rule--under-logo { left: 20px; top: 178px; width: 420px; height: 1.5px; }
  .rule--mid { left: 0; top: 478px; width: 500px; height: 1.5px; }
  .rule--bottom { left: 40px; top: 620px; width: 460px; height: 1.5px; }
  .inside__logo { position: absolute; left: 150px; top: 95px; width: 260px; display: flex; justify-content: center; }
  .inside .wordmark { color: var(--brand-blue-light); font-size: 24px; }
  .inside .wordmark__square { background: var(--brand-blue-light); }
  .project-photo { position: absolute; left: 55px; top: 195px; width: 420px; height: 245px; background: linear-gradient(180deg, #c9d2d6 0%, #7f9060 45%, #b8a478 75%, #9c8f7c 100%); }
  .photo-bracket { position: absolute; left: 470px; top: 240px; width: 20px; height: 95px; border-top: 8px solid var(--line-blue); border-right: 8px solid var(--line-blue); }
  .accent-bar { position: absolute; left: 15px; top: 410px; width: 280px; height: 45px; background: var(--bar-grey); }
  .hazard-bar { position: absolute; left: 0; top: 440px; width: 235px; height: 28px; }
  .inside__intro { position: absolute; left: 50px; right: 20px; top: 505px; text-align: center; color: var(--text-grey); font-size: 18px; line-height: 1.3; }
</style>
</head>
<body>
  <main class="spread">
    <section class="page cover">
      <div class="cover__panel">
        <div class="wordmark"><span class="wordmark__square"></span>Brovan Builders</div>
      </div>
      <div class="cover__contact">
        <div class="contact-line contact-line--phone">
          <svg class="icon-phone" viewBox="0 0 30 30" aria-hidden="true">
            <rect width="30" height="30" rx="6" fill="#fff"/>
            <path d="M10 7c1 0 3 3 3 4s-2 1-2 2 3 5 4 5 1-2 2-2 4 2 4 3-2 4-4 4C11 23 7 14 7 10c0-2 2-3 3-3z" fill="#1363b4"/>
          </svg>
          <span>(818.502.6617)</span>
        </div>
        <div class="contact-line contact-line--email">
          <svg class="icon-globe" viewBox="0 0 16 16" aria-hidden="true" fill="none" stroke="#fff" stroke-width="1">
            <circle cx="8" cy="8" r="7"/><ellipse cx="8" cy="8" rx="3" ry="7"/><path d="M1 8h14M2 4.5h12M2 11.5h12"/>
          </svg>
          <span>contact@brovanbuildersinc.example</span>
        </div>
      </div>
    </section>

    <section class="page inside">
      <span class="rule rule--vertical"></span>
      <span class="rule rule--dot"></span>
      <div class="inside__logo">
        <div class="wordmark"><span class="wordmark__square"></span>Brovan Builders</div>
      </div>
      <span class="rule rule--under-logo"></span>
      <div class="project-photo" role="img" aria-label="Photo of an excavator clearing rock and debris on a hillside site with trees"></div>
      <span class="photo-bracket"></span>
      <span class="accent-bar"></span>
      <svg class="hazard-bar" viewBox="0 0 235 28" aria-hidden="true">
        <rect width="235" height="28" fill="#fff"/>
        <g fill="#2f86d8">
          <polygon points="0,28 12,0 40,0 28,28"/>
          <polygon points="52,28 64,0 92,0 80,28"/>
          <polygon points="104,28 116,0 144,0 132,28"/>
          <polygon points="156,28 168,0 196,0 184,28"/>
          <polygon points="208,28 220,0 235,0 235,28"/>
        </g>
        <rect x=".5" y=".5" width="234" height="27" fill="none" stroke="#2f86d8"/>
      </svg>
      <span class="rule rule--mid"></span>
      <p class="inside__intro">Brovan Builders is a leading construction firm established in 2019, driven by a commitment to excellence and innovation in the building industry.</p>
      <span class="rule rule--bottom"></span>
    </section>
  </main>
</body>
</html>
```